Web Design Project

We need a web design for a new company. We have a logo, and we've identified the style of a website that we'd like to adapt (www.brindlemoor.com). We do not sell to the public. The purpose of the site is (1) to allow our appointed sales partners to log in to our proprietary database system and (2) to provide a basic web presence and some basic information about our company.

We sell business insurance through independent agents - our sales partners.

Please do not use a photo of a person/s as a central design element, or at all.

Target Market(s)

The purpose of the site is not to sell, but to provide a professional landing page for a log in and some basic company information.

Industry/Entity Type

Business

Requirements
Must have
• A professional look. Agent log in must be central, clear and easy. Use of our logo and our colors.
Should not have
• Photos of people

```html
<!DOCTYPE html>
<html lang="en">
<head>
<meta charset="utf-8">
<title>Larkfield Insurance</title>
<link href="https://fonts.googleapis.com/css2?family=Arimo:wght@400;700&family=Arvo:wght@700&display=swap" rel="stylesheet">
<style>
:root{
  --navy:#0a4669;
  --navy-dark:#063650;
  --blue:#0b5d8a;
  --bright:#1486c4;
  --page:#efefef;
  --white:#ffffff;
  --ink:#2b2b2b;
  --body:#3a3a3a;
  --field:#ececec;
  --line:#d6d6d6;
}
*{box-sizing:border-box;margin:0;padding:0}
html,body{width:947px;height:1200px;overflow:hidden}
body{background:var(--page);font-family:"Arimo",Arial,sans-serif;color:var(--ink);position:relative}
.abs{position:absolute}

/* header */
.brand{left:101px;top:44px;display:flex;align-items:center;gap:8px;color:var(--navy);font-weight:700;font-size:16px;letter-spacing:.5px}
.brand-mark{width:16px;height:16px;background:var(--navy)}
.phone{left:666px;top:0;width:186px;height:35px;background:var(--navy);border-radius:0 0 4px 4px;color:var(--white);font-weight:700;font-size:15px;display:flex;align-items:center;gap:12px;padding-left:12px}
.phone-icon{width:19px;height:19px;background:var(--white);border-radius:3px;display:flex;align-items:center;justify-content:center}
.tagline{left:560px;top:62px;width:292px;text-align:right;font-size:11px;font-weight:700;color:var(--blue)}
.btn{background:var(--navy);color:var(--white);font-weight:700;border-radius:4px;display:flex;align-items:center;justify-content:center;text-transform:uppercase}

/* nav */
.nav{left:0;top:131px;width:947px;height:31px;background:var(--navy);display:flex;padding-left:94px}
.nav a{color:var(--white);text-decoration:none;font-weight:700;font-size:11.5px;display:flex;align-items:center;padding:0 21px;border-right:1px solid #1c5f86}
.nav a:last-child{border-right:0}
.nav a.active{background:var(--blue);padding:0 16px}

/* slider */
.slider{left:94px;top:174px;width:758px;height:306px;background:var(--white);padding:8px;box-shadow:0 14px 14px -10px rgba(0,0,0,.25)}
.slide{width:742px;height:290px;background:linear-gradient(180deg,#6f8fb6 0%,#5d7ca6 45%,#8aa3c0 75%,#c9ccd2 100%)}
.arrow{top:306px}

/* agent login, centred on the hero */
.agent-login{left:303px;top:224px;width:340px;height:206px;background:rgba(255,255,255,.96);border-radius:4px;box-shadow:0 6px 18px rgba(0,0,0,.3);padding:18px 22px}
.agent-login h2{font-family:"Arvo",Georgia,serif;font-size:17px;color:var(--navy);letter-spacing:.3px}
.agent-login .sub{font-size:10px;color:#555;margin-top:4px}
.agent-login input{display:block;width:296px;height:28px;margin-top:10px;border:1px solid var(--line);border-radius:3px;background:var(--white);font:11px "Arimo",sans-serif;padding-left:9px;color:#333}
.agent-login .row{display:flex;align-items:center;justify-content:space-between;margin-top:12px}
.agent-login .links{font-size:10px;font-weight:700;display:flex;gap:16px}
.agent-login .links .reg{color:var(--blue)}
.agent-login .btn{width:86px;height:30px;font-size:12px}

/* features */
.feature{top:521px;width:237px;height:89px;border-radius:4px;background:linear-gradient(180deg,var(--blue),var(--navy-dark));color:var(--white);box-shadow:0 10px 12px -8px rgba(0,0,0,.35)}
.feature.mid{background:linear-gradient(180deg,#1a9ad6,#0a6ea8)}
.feature .icon{position:absolute;left:6px;top:14px;width:56px;height:56px;border-radius:8px}
.feature h3{position:absolute;left:69px;top:14px;font-family:"Arvo",Georgia,serif;font-size:17px;letter-spacing:.5px}
.feature p{position:absolute;left:69px;top:39px;width:165px;font-size:9px;line-height:11.5px}

/* side panels */
.panel{background:var(--white);border:1px solid #e2e2e2;border-radius:4px;box-shadow:0 8px 10px -8px rgba(0,0,0,.25)}
.search{left:94px;top:639px;width:238px;height:303px;padding:15px 9px}
.field{height:25px;background:var(--field);border:1px solid var(--line);border-radius:3px;font-size:9.5px;display:flex;align-items:center;padding-left:8px;position:relative;margin-bottom:15px}
.field.sel::after{content:"";position:absolute;right:0;top:3px;width:24px;height:17px;border-left:1px solid var(--line)}
.field.sel svg{position:absolute;right:8px;top:9px}
.label{font-size:9.5px;font-weight:700;margin:-5px 0 9px 3px}
.search .actions{display:flex;gap:14px;margin-top:-3px}
.search .btn{height:28px;font-size:11.5px}

.video{left:94px;top:962px;width:238px;height:170px;padding:9px}
.video-frame{width:220px;height:140px;background:linear-gradient(180deg,#9ab7d8 0%,#c4d2e0 50%,#a58f5b 85%);position:relative}
.play{position:absolute;left:87px;top:44px}
.controls{height:7px;margin-top:2px;border:1px solid #bbb;background:#f6f6f6;font-size:5px;display:flex;align-items:center;gap:4px;padding:0 3px}
.controls .track{flex:1;height:1px;background:#999}

/* main */
.welcome{left:355px;top:640px;width:498px}
.heading{font-family:"Arvo",Georgia,serif;font-size:18px;color:#333;letter-spacing:.3px}
.lead{font-size:14px;font-weight:700;color:var(--blue);margin-top:16px}
.welcome p.body{font-size:11px;line-height:13.3px;color:var(--body);margin-top:10px}
.welcome p.body+p.body{margin-top:13px}
.rule{left:355px;width:497px;height:1px;background:var(--line)}
.more{left:781px;top:966px;font-size:9px;font-weight:700;color:var(--blue);display:flex;gap:7px;align-items:center}
.services-title{left:357px;top:1003px}
.services{left:357px;top:1049px;display:grid;grid-template-columns:182px 182px 150px;row-gap:14px;font-size:11px;color:#333}
.services li{list-style:none;display:flex;align-items:center;gap:6px;height:14px;white-space:nowrap}

/* footer */
.footer{left:0;top:1150px;width:947px;height:50px;background:var(--navy);color:var(--white);font-size:9.5px}
.footer .copy{position:absolute;left:95px;top:10px;line-height:19px}
.social{position:absolute;left:725px;top:15px;display:flex;gap:8px}
.social span{width:24px;height:24px;border-radius:3px}
</style>
</head>
<body>

<header>
  <div class="abs brand"><span class="brand-mark"></span>LARKFIELD INSURANCE</div>
  <div class="abs phone">
    <span class="phone-icon"><svg width="11" height="11" viewBox="0 0 24 24"><path fill="#0a4669" d="M6.6 10.8a15 15 0 0 0 6.6 6.6l2.2-2.2c.3-.3.7-.4 1-.2 1.1.4 2.3.6 3.6.6.6 0 1 .4 1 1V20c0 .6-.4 1-1 1A17 17 0 0 1 3 4c0-.6.4-1 1-1h3.5c.6 0 1 .4 1 1 0 1.3.2 2.5.6 3.6.1.3 0 .7-.2 1z"/></svg></span>
    (000) 000 - 0000
  </div>
  <div class="abs tagline">Business insurance through independent agents</div>
</header>

<nav class="abs nav">
  <a class="active">HOME</a><a>ABOUT US</a><a>RAISE CAPITAL</a><a>INVESTORS</a><a>SEARCH</a><a>FAQ'S</a><a>BLOG</a><a>CONTACT US</a>
</nav>

<section class="abs slider">
  <div class="slide" role="img" aria-label="Slideshow image of a calm seashore"></div>
</section>
<svg class="abs arrow" style="left:110px" width="26" height="42" viewBox="0 0 26 42"><path d="M21 4 6 21l15 17" fill="none" stroke="#111" stroke-width="6" stroke-linejoin="round" stroke-linecap="round"/></svg>
<svg class="abs arrow" style="left:812px" width="26" height="42" viewBox="0 0 26 42"><path d="M5 4l15 17L5 38" fill="none" stroke="#111" stroke-width="6" stroke-linejoin="round" stroke-linecap="round"/></svg>

<form class="abs agent-login">
  <h2>AGENT LOGIN</h2>
  <p class="sub">Sales partners: sign in to the partner database.</p>
  <input type="text" value="User name">
  <input type="text" value="Password">
  <div class="row">
    <div class="links"><span>Forgot password?</span><span class="reg">Register now</span></div>
    <span class="btn">Login</span>
  </div>
</form>

<section>
  <div class="abs feature" style="left:94px">
    <div class="icon" role="img" aria-label="Illustration of a joystick on a grey base" style="background:linear-gradient(180deg,#666,#d8d8d8)"></div>
    <h3>ACCESSIBILITY</h3>
    <p>At vero eos et accusamus et iustoodio dignissimos ducimus qui blanditiraen-tiumum lipsum&nbsp; dolor</p>
  </div>
  <div class="abs feature mid" style="left:355px">
    <div class="icon" role="img" aria-label="Illustration of a thumbs-up on a gold seal" style="background:radial-gradient(circle,#f3e5a0 30%,#d6b431 70%,transparent 72%)"></div>
    <h3>GUARANTEE</h3>
    <p>At vero eos et accusamus et iustoodio dignissimos ducimus qui blanditiraen-tiumum lipsum&nbsp; dolor</p>
  </div>
  <div class="abs feature" style="left:614px">
    <div class="icon" role="img" aria-label="Illustration of a money bag" style="background:radial-gradient(circle at 50% 60%,#eadb8c 35%,#c8b257 60%,transparent 63%)"></div>
    <h3>AFFILIATES</h3>
    <p>At vero eos et accusamus et iustoodio dignissimos ducimus qui blanditiraen-tiumum lipsum&nbsp; dolor</p>
  </div>
</section>

<aside>
  <form class="abs panel search">
    <div class="field">Keywords</div>
    <div class="field">Zip Code</div>
    <div class="label">Filter by Location:</div>
    <div class="field sel">Select State/Province<svg width="8" height="5" viewBox="0 0 8 5"><path d="M1 1l3 3 3-3" fill="none" stroke="#aaa" stroke-width="1.3"/></svg></div>
    <div class="label">Filter by Industry:</div>
    <div class="field sel">Select an Industry<svg width="8" height="5" viewBox="0 0 8 5"><path d="M1 1l3 3 3-3" fill="none" stroke="#aaa" stroke-width="1.3"/></svg></div>
    <div class="label">Filter by Capital Needs:</div>
    <div class="field sel">Select Capital Amount<svg width="8" height="5" viewBox="0 0 8 5"><path d="M1 1l3 3 3-3" fill="none" stroke="#aaa" stroke-width="1.3"/></svg></div>
    <div class="actions">
      <span class="btn" style="width:78px">SEARCH</span>
      <span class="btn" style="width:126px">VIEW ALL RESULTS</span>
    </div>
  </form>

  <div class="abs panel video">
    <div class="video-frame" role="img" aria-label="Video still of open country under a blue sky">
      <svg class="play" width="44" height="44" viewBox="0 0 44 44"><circle cx="22" cy="22" r="21" fill="#666" fill-opacity=".8"/><path d="M16 12l16 10-16 10z" fill="#eee"/></svg>
    </div>
    <div class="controls"><span>▶ ■</span><span>00:00</span><span class="track"></span><span>00:10</span><span>⤢ ◀</span></div>
  </div>
</aside>

<main>
  <article class="abs welcome">
    <h2 class="heading">WELCOME</h2>
    <p class="lead">As businesses look to save money in an ever-challenging economy,</p>
    <p class="body">one way to save on insurance is by obtaining insurance online and finding an agent wlipsum lipho has your best interests in mind when it comes to getting free insurance quotes.one way to save on insur-ance is by obtaining insurance online and finding an agent wlipsum lipho has your best interests mind when it comes to getting free insurance quotes.</p>
    <p class="body">tis et quasi architecto beatae vitae dicta sunt explicabo. Nemo enim ipsam voluptatem quia voluptas sit aspernatur aut odit aut fugit, sed quia consequuntur magni dolores eos qui ratione voluptatem sequi nesciunt. Neque porro quisquam est, qui dolorem ipsum quia dolor sit amet, consectetur, adipisci velit, sed quia non numquam eius modi tempora incidunt ut labore et dolore magnam aliquam quaerat voluptatem. Ut enim ad minima veniam, quis nostrum exercitationem ullam corporis suscipit laboriosam, nisi ut aliquid ex ea commodi consequatur? Quis autem vel eum iure reprehenderit qui in ea voluptate velit esse quam nihil molestiae consequatur, vel illum qui dolorem eum fugiat quo voluptas nulla</p>
    <p class="body">tis et quasi architecto beatae vitae dicta sunt explicabo. Nemo enim ipsam voluptatem quia voluptas sit aspernatur aut odit aut fugit, sed quia consequuntur magni dolores eos qui ratione voluptatem sequi nesciunt. Neque porro quisquam est, qui dolorem ipsum quia dolor sit amet, consectetur, adipisci velit, sed quia non numquam eius modi tempora incidunt ut labore et dolore magnam aliquam</p>
  </article>
  <div class="abs rule" style="top:954px"></div>
  <div class="abs more">READ MORE <svg width="6" height="8" viewBox="0 0 6 8"><path d="M0 0l6 4-6 4z" fill="#0b5d8a"/></svg></div>
  <div class="abs rule" style="top:986px"></div>

  <h2 class="abs heading services-title">SERVICES</h2>
  <ul class="abs services">
    <li><svg width="7" height="10" viewBox="0 0 7 10"><path d="M1 1l4 4-4 4" fill="none" stroke="#444" stroke-width="2"/></svg>Commercial Property</li>
    <li><svg width="7" height="10" viewBox="0 0 7 10"><path d="M1 1l4 4-4 4" fill="none" stroke="#444" stroke-width="2"/></svg>General Liability</li>
    <li><svg width="7" height="10" viewBox="0 0 7 10"><path d="M1 1l4 4-4 4" fill="none" stroke="#444" stroke-width="2"/></svg>Fleet &amp; Auto</li>
    <li><svg width="7" height="10" viewBox="0 0 7 10"><path d="M1 1l4 4-4 4" fill="none" stroke="#444" stroke-width="2"/></svg>Workers' Comp</li>
    <li><svg width="7" height="10" viewBox="0 0 7 10"><path d="M1 1l4 4-4 4" fill="none" stroke="#444" stroke-width="2"/></svg>Professional Liability</li>
    <li><svg width="7" height="10" viewBox="0 0 7 10"><path d="M1 1l4 4-4 4" fill="none" stroke="#444" stroke-width="2"/></svg>Cyber Cover</li>
    <li><svg width="7" height="10" viewBox="0 0 7 10"><path d="M1 1l4 4-4 4" fill="none" stroke="#444" stroke-width="2"/></svg>Business Interruption</li>
    <li><svg width="7" height="10" viewBox="0 0 7 10"><path d="M1 1l4 4-4 4" fill="none" stroke="#444" stroke-width="2"/></svg>Directors &amp; Officers</li>
    <li><svg width="7" height="10" viewBox="0 0 7 10"><path d="M1 1l4 4-4 4" fill="none" stroke="#444" stroke-width="2"/></svg>Key Person</li>
  </ul>
</main>

<footer class="abs footer">
  <div class="copy">© 2010 Larkfield Insurance. All Rights Reserved.<br>Privacy Policy | User Agreement | T&amp;C</div>
  <div class="social" aria-label="Social links">
    <span style="background:#4a6aa8"></span><span style="background:#5cc3e6"></span><span style="background:#3c8ccc"></span><span style="background:#f08a24"></span>
  </div>
</footer>

</body>
</html>
```